Brightmill Data Works

Our company is about IT hardwares and IT solutions. IT hardware such as PC, RAMS, storage and servers. IT solutions such as project management, BA. We are also selling new technology too.

Target Market(s)

Consumer, Small to Medium Business, Corporate

Requirements
Must have
• The business card must have the following:
• Name:
• Title:
• Contact Number:
• Email address:
• Website:
• Color: Must match the logo color upgrade

```html
<!DOCTYPE html>
<html lang="en">
<head>
<meta charset="utf-8">
<title>Brightmill Data Works – Business Card</title>
<link rel="stylesheet" href="https://fonts.googleapis.com/css2?family=Open+Sans:wght@400;600;700&display=swap">
<style>
  :root {
    --backdrop: #676767;
    --orange-light: #de9a42;
    --orange-deep: #c3682a;
    --charcoal: #474747;
    --ink: #3f3f3f;
    --paper: #ffffff;
    --card-w: 443px;
    --card-h: 265px;
  }
  html, body {
    margin: 0;
    padding: 0;
    width: 1200px;
    height: 802px;
    overflow: hidden;
    background: var(--backdrop);
    font-family: "Open Sans", Arial, sans-serif;
  }
  .canvas {
    position: relative;
    width: 1200px;
    height: 802px;
  }
  .card {
    position: absolute;
    top: 274px;
    width: var(--card-w);
    height: var(--card-h);
    overflow: hidden;
  }
  .card--front {
    left: 135px;
    background: linear-gradient(180deg, var(--orange-light) 0%, var(--orange-deep) 100%);
  }
  .card--back {
    left: 624px;
    background: var(--paper);
  }
  .front-panel {
    position: absolute;
    left: 0;
    top: 0;
    width: 100%;
    height: 100%;
  }
  .identity {
    position: absolute;
    right: 26px;
    top: 69px;
    text-align: right;
    color: var(--paper);
  }
  .identity__name {
    margin: 0;
    font-size: 16px;
    font-weight: 600;
    line-height: 18px;
    letter-spacing: 0.1px;
  }
  .identity__title {
    margin: 0;
    font-size: 13px;
    font-weight: 400;
    line-height: 16px;
  }
  .contact {
    position: absolute;
    right: 26px;
    top: 148px;
    margin: 0;
    padding: 0;
    list-style: none;
    color: var(--paper);
    font-size: 12.5px;
    line-height: 16.5px;
    text-align: right;
  }
  .contact__item {
    display: flex;
    justify-content: flex-end;
    align-items: center;
    gap: 3px;
  }
  .contact__icon {
    width: 9px;
    height: 9px;
    flex: none;
  }
  .brand {
    position: absolute;
    left: 0;
    right: 0;
    top: 112px;
    display: flex;
    justify-content: center;
    align-items: center;
    gap: 10px;
  }
  .brand__square {
    width: 18px;
    height: 18px;
    background: var(--orange-deep);
  }
  .brand__name {
    margin: 0;
    font-size: 24px;
    font-weight: 700;
    color: var(--ink);
    letter-spacing: 0.5px;
    text-transform: uppercase;
  }
</style>
</head>
<body>
<main class="canvas">
  <section class="card card--front" aria-label="Business card front">
    <svg class="front-panel" viewBox="0 0 443 265" preserveAspectRatio="none" aria-hidden="true">
      <polygon points="0,0 60,0 60,30 170,130 250,210 250,265 0,265" fill="var(--charcoal)"/>
    </svg>
    <div class="identity">
      <h1 class="identity__name">DANIEL HARPER</h1>
      <p class="identity__title">Managing Director</p>
    </div>
    <ul class="contact">
      <li class="contact__item">044-987 654 321
        <svg class="contact__icon" viewBox="0 0 10 10" aria-hidden="true"><path d="M1 3 Q5 0 9 3 L8 4.5 L6.5 3.8 L6.5 3 Q5 2.5 3.5 3 L3.5 3.8 L2 4.5 Z M2.5 5 H7.5 L8.5 9 H1.5 Z" fill="#fff"/></svg>
      </li>
      <li class="contact__item">info@brightmill.com
        <svg class="contact__icon" viewBox="0 0 10 10" aria-hidden="true"><rect x="0.5" y="2" width="9" height="6.5" fill="#fff"/><path d="M0.8 2.3 L5 5.6 L9.2 2.3" stroke="var(--orange-deep)" stroke-width="0.9" fill="none"/></svg>
      </li>
      <li class="contact__item">www.brightmilldata.com
        <svg class="contact__icon" viewBox="0 0 10 10" aria-hidden="true"><circle cx="5" cy="5" r="4.5" fill="#fff"/><path d="M3 3.5 Q4.5 3 5 4.5 Q4 6 5.5 7.5 M6.5 2.5 Q7.5 4 7 5" stroke="var(--orange-deep)" stroke-width="1" fill="none"/></svg>
      </li>
    </ul>
  </section>

  <section class="card card--back" aria-label="Business card back">
    <div class="brand">
      <span class="brand__square" aria-hidden="true"></span>
      <p class="brand__name">Brightmill Data Works</p>
    </div>
  </section>
</main>
</body>
</html>
```